Im open to ideas.. I was thinking on my business cards aswell as my logo. a place for my name. email. phone number and abn..

ive attched a file with my business logo. which i dont love the colours.. i was think a dark background with charcoal letters so something along those colour schumes but im open to ideas..

BRM Constructions

```html
<!DOCTYPE html>
<html lang="en">
<head>
<meta charset="utf-8">
<title>BRM Constructions – Business Cards</title>
<link rel="stylesheet" href="https://fonts.googleapis.com/css2?family=Montserrat:wght@700&family=Open+Sans:wght@400;600&display=swap">
<style>
  :root {
    --page-bg: #3a3431;
    --card-bg: #0d0d0d;
    --accent-yellow: #f2c21b;
    --silver: #c9c9c9;
    --text-light: #d8d8d8;
    --divider: #6b5710;
  }
  * { margin: 0; padding: 0; box-sizing: border-box; }
  html, body {
    width: 1200px;
    height: 900px;
    overflow: hidden;
    background: var(--page-bg);
    font-family: "Open Sans", sans-serif;
  }
  .card-set {
    position: absolute;
    top: 0; left: 0;
    width: 1200px; height: 900px;
    display: flex;
    align-items: center;
    justify-content: center;
    gap: 40px;
  }
  .card {
    width: 540px;
    height: 309px;
    background: var(--card-bg);
    border-radius: 3px;
    position: relative;
    overflow: hidden;
  }

  /* Front: name-mark left, contact details right */
  .card-front { display: flex; }
  .front-brand {
    width: 54%;
    display: flex;
    align-items: center;
    justify-content: center;
    gap: 10px;
  }
  .brand-square {
    width: 14px; height: 14px;
    background: var(--accent-yellow);
  }
  .brand-name {
    font-family: "Montserrat", sans-serif;
    font-weight: 700;
    font-size: 24px;
    color: var(--silver);
    letter-spacing: 0.5px;
  }
  .front-divider {
    width: 1px;
    margin: 60px 0;
    background: var(--divider);
  }
  .contact-block {
    flex: 1;
    padding: 72px 0 0 26px;
    color: var(--text-light);
    font-size: 12.5px;
  }
  .person-name {
    color: var(--accent-yellow);
    font-weight: 600;
    font-size: 15px;
    line-height: 1.2;
  }
  .person-role { font-size: 12px; margin-bottom: 20px; }
  .abn { margin-bottom: 20px; }
  .abn-label { color: var(--accent-yellow); font-weight: 600; }
  .contact-list { list-style: none; }
  .contact-list li {
    display: flex;
    align-items: center;
    gap: 10px;
    line-height: 19px;
  }
  .contact-icon { width: 10px; height: 10px; fill: var(--accent-yellow); flex: none; }

  /* Back: centred name-mark */
  .card-back {
    display: flex;
    align-items: center;
    justify-content: center;
  }
  .card-back .brand-name { font-size: 30px; }
</style>
</head>
<body>
  <main class="card-set">
    <section class="card card-front" aria-label="Business card front">
      <div class="front-brand">
        <span class="brand-square"></span>
        <span class="brand-name">BRM Constructions</span>
      </div>
      <div class="front-divider"></div>
      <div class="contact-block">
        <p class="person-name">Daniel Harper</p>
        <p class="person-role">Managing Director</p>
        <p class="abn"><span class="abn-label">ABN :</span> 12345678</p>
        <ul class="contact-list">
          <li>
            <svg class="contact-icon" viewBox="0 0 10 10"><path d="M2 0.5 3.6 2.6 2.7 3.6C3.3 5 4.9 6.7 6.4 7.3L7.4 6.4 9.5 8 8.5 9.5C4.5 9.3 0.7 5.5 0.5 1.5Z"/></svg>
            044-987 654 321
          </li>
          <li>
            <svg class="contact-icon" viewBox="0 0 10 10"><path d="M0.5 2h9v6h-9z M0.5 2 5 5.5 9.5 2" fill="var(--accent-yellow)"/><path d="M0.8 2.3 5 5.4 9.2 2.3" stroke="#0d0d0d" stroke-width="0.8" fill="none"/></svg>
            info@brmbuild.com
          </li>
          <li>
            <svg class="contact-icon" viewBox="0 0 10 10"><circle cx="5" cy="5" r="4.5"/><path d="M5 0.5v9M0.5 5h9M2 2.3c2 1 4 1 6 0M2 7.7c2-1 4-1 6 0" stroke="#0d0d0d" stroke-width="0.6" fill="none"/></svg>
            www.brmbuild.com
          </li>
        </ul>
      </div>
    </section>

    <section class="card card-back" aria-label="Business card back">
      <span class="brand-name">BRM Constructions</span>
    </section>
  </main>
</body>
</html>
```